Brindlewick Solutions Ltd

I'd like to create a company letterhead for the attached logo in word format.

I'd like to emphasis the icon in large translucent state from the left corner and ensure that the letterhead colouring matches the colour palette of the current logo with a contrast so it's clear to see. I've attached a copy of our sister company page on the app for reference.

```html
<!DOCTYPE html>
<html lang="en">
<head>
<meta charset="utf-8">
<title>Brindlewick Solutions Ltd – Letterhead</title>
<link rel="stylesheet" href="https://fonts.googleapis.com/css2?family=Lato:wght@400;700&display=swap">
<style>
  :root {
    --backdrop: #d9d9d9;
    --paper: #ffffff;
    --header-bg: #111111;
    --teal: #14b8a6;
    --teal-faint: #e3f5f2;
    --divider: #3a3a3a;
    --text-light: #ffffff;
  }
  * { box-sizing: border-box; margin: 0; padding: 0; }
  html, body {
    width: 1061px; height: 1200px; overflow: hidden;
    background: var(--backdrop);
    font-family: "Lato", sans-serif;
  }
  .letterhead {
    position: absolute; left: 106px; top: 0;
    width: 848px; height: 1200px;
    background: var(--paper);
    overflow: hidden;
  }
  .header {
    position: absolute; left: 0; top: 0;
    width: 100%; height: 183px;
    background: var(--header-bg);
  }
  .header-rule {
    position: absolute; left: 0; top: 187px;
    width: 100%; height: 5px;
    background: var(--teal);
  }
  .brand {
    position: absolute; left: 64px; top: 70px;
    display: flex; align-items: center; gap: 12px;
  }
  .brand-dot {
    width: 44px; height: 44px; border-radius: 50%;
    background: var(--teal);
  }
  .brand-name {
    font-size: 30px; font-weight: 400; color: var(--teal);
    letter-spacing: 0.2px;
  }
  .divider {
    position: absolute; top: 71px;
    width: 1px; height: 61px;
    background: var(--divider);
  }
  .divider--first { left: 331px; }
  .divider--second { left: 550px; }
  .address, .contact {
    position: absolute; top: 73px;
    font-size: 14px; line-height: 18.7px;
    color: var(--text-light);
    list-style: none;
  }
  .address { left: 366px; }
  .address .company { color: var(--teal); }
  .contact { left: 584px; }
  .contact li { display: flex; align-items: center; gap: 7px; }
  .contact svg { width: 10px; height: 10px; flex: none; fill: var(--teal); }
  .watermark {
    position: absolute; left: -82px; top: 697px;
    width: 474px; height: 474px; border-radius: 50%;
    background: var(--teal-faint);
  }
  .sheen {
    position: absolute; left: 0; top: 425px;
    width: 100%; height: 420px;
    background: linear-gradient(160deg, rgba(0,0,0,0.03) 0%, rgba(0,0,0,0) 45%);
  }
</style>
</head>
<body>
  <main class="letterhead">
    <header class="header">
      <div class="brand">
        <span class="brand-dot"></span>
        <span class="brand-name">Brindlewick</span>
      </div>
      <span class="divider divider--first"></span>
      <address class="address">
        <span class="company">Brindlewick Solutions Ltd</span><br>
        4170 Harrow Lane<br>
        Millbrook, CT 06455
      </address>
      <span class="divider divider--second"></span>
      <ul class="contact">
        <li>
          <svg viewBox="0 0 10 10" aria-hidden="true"><path d="M2 0.5 L3.6 0.5 L4.2 3 L3 3.8 Q4 6 6.2 7 L7 5.8 L9.5 6.4 L9.5 8 Q9.5 9.5 8 9.5 Q0.5 9 0.5 2 Q0.5 0.5 2 0.5Z"/></svg>
          (555) 318-4426
        </li>
        <li>
          <svg viewBox="0 0 10 10" aria-hidden="true"><path d="M0 2 L5 5.5 L10 2 L10 8.5 L0 8.5Z M0.5 1.5 L9.5 1.5 L5 4.6Z"/></svg>
          info@brindlewicksolutions.com
        </li>
        <li>
          <svg viewBox="0 0 10 10" aria-hidden="true"><circle cx="5" cy="5" r="4.6"/></svg>
          brindlewicksolutions.com
        </li>
      </ul>
    </header>
    <div class="header-rule"></div>
    <div class="sheen"></div>
    <div class="watermark"></div>
  </main>
</body>
</html>
```